Consulting company business cards

We have a base design, but would be willing to update. We have a new logo/"tag" that needs to be added. Current business card design is attached for reference into our "style."

Industry/Entity Type

Business

Contact Information for Business Card

Should contain name and title, office number, mobile number if appropriate, e-mail, website, physical address, and company logo.

Font styles to use
Other font styles liked:
• See current card design on KorvandBCard

Colors
0455a3
85acd3
aaaaaa

Requirements
Must have
• Our colors are navy blue, gray, and a lighter blue
Nice to have
• Design that I can easily drop in new names/titles as we hire employees.

```html
<!DOCTYPE html>
<html lang="en">
<head>
<meta charset="utf-8">
<title>Brinmoor – Business Card</title>
<link href="https://fonts.googleapis.com/css2?family=Source+Sans+3:wght@400;600;700&display=swap" rel="stylesheet">
<style>
  :root {
    --stage: #000000;
    --card-front: #f3f3f3;
    --navy: #0b2f4e;
    --ink: #1c1c1c;
    --light-blue: #85acd3;
    --gray: #9a9a9a;
    --back-light: #73a3c2;
    --back-mid: #4d7e9d;
    --back-deep: #3a6886;
    --back-dark: #1b4764;
    --white: #ffffff;
  }
  * { margin: 0; padding: 0; box-sizing: border-box; }
  html, body { width: 1200px; height: 900px; overflow: hidden; background: var(--stage); }
  body { position: relative; font-family: "Source Sans 3", "Myriad Pro", sans-serif; }

  .card { position: absolute; top: 200px; width: 310px; height: 502px; overflow: hidden; }
  .card-front {
    left: 265px; background: var(--card-front);
    border-radius: 62px 0 72px 0;
  }
  .card-back {
    left: 641px; width: 309px;
    border-radius: 0 62px 0 72px;
    background:
      radial-gradient(ellipse 120px 90px at 55% 43%, rgba(45,90,118,0.55), transparent 100%),
      radial-gradient(ellipse 200px 160px at 30% 30%, rgba(60,105,135,0.5), transparent 100%),
      linear-gradient(200deg, var(--back-light) 0%, var(--back-mid) 35%, var(--back-deep) 60%, var(--back-mid) 75%, var(--back-dark) 100%);
  }

  .wordmark { position: absolute; left: 25px; display: flex; align-items: center; gap: 8px; }
  .wordmark-name { font-weight: 700; font-size: 40px; line-height: 1; letter-spacing: 0; white-space: nowrap; }
  .wordmark-dot { width: 40px; height: 40px; border-radius: 50%; flex: none; }
  .tagline { position: absolute; left: 26px; font-size: 12.5px; letter-spacing: 2.3px; text-transform: uppercase; white-space: nowrap; }

  .card-front .wordmark { top: 66px; }
  .card-front .wordmark-name { color: var(--navy); }
  .card-front .wordmark-dot { background: var(--light-blue); }
  .card-front .tagline { top: 119px; color: var(--gray); }

  .card-back .wordmark { left: 35px; top: 368px; }
  .card-back .wordmark-name { color: var(--white); }
  .card-back .wordmark-dot { background: var(--white); }
  .card-back .tagline { left: 36px; top: 421px; color: var(--white); }

  .person { position: absolute; left: 25px; top: 257px; }
  .person-name { font-size: 19px; font-weight: 600; color: var(--navy); line-height: 1.2; }
  .person-title { font-size: 14px; color: var(--ink); line-height: 1.3; }

  .address { position: absolute; left: 25px; top: 320px; font-size: 14px; color: var(--ink); line-height: 21px; font-style: normal; }

  .contacts { position: absolute; left: 25px; top: 374px; list-style: none; }
  .contacts li { display: flex; align-items: center; gap: 8px; font-size: 14px; color: var(--ink); height: 21px; }
  .contacts svg { width: 11px; height: 11px; fill: var(--navy); flex: none; }
</style>
</head>
<body>
  <section class="card card-front">
    <div class="wordmark">
      <span class="wordmark-name">BRINMOOR</span>
      <span class="wordmark-dot"></span>
    </div>
    <p class="tagline">A Cloud Consulting Company</p>

    <div class="person">
      <p class="person-name">Hana Korvand</p>
      <p class="person-title">Office Manager</p>
    </div>

    <address class="address">1187 N Larkspur Ave Fairbridge<br>Ohio 45012</address>

    <ul class="contacts">
      <li><svg viewBox="0 0 12 12"><path d="M2.5 0.5l2 2.2-1 1.3c.7 1.6 1.9 2.8 3.5 3.5l1.3-1 2.2 2-1.2 2.2C5 10.5 1.5 7 .3 1.7z"/></svg>555.204.3816</li>
      <li><svg viewBox="0 0 12 12"><path d="M3 0h5l1 1v3H3z M1 4.5h10v6H1z" /><rect x="3" y="6" width="6" height="1" fill="#f3f3f3"/><rect x="3" y="8" width="6" height="1" fill="#f3f3f3"/></svg>555.204.3870</li>
      <li><svg viewBox="0 0 12 12"><path d="M0 2h12v8H0z"/><path d="M0.5 2.5L6 6.8 11.5 2.5" fill="none" stroke="#f3f3f3" stroke-width="1"/></svg>hkorvand@brinmoortech.com</li>
      <li><svg viewBox="0 0 12 12"><circle cx="6" cy="6" r="5.5"/><path d="M6 0.8v10.4M0.8 6h10.4M6 0.8c-2.6 2.8-2.6 7.6 0 10.4M6 0.8c2.6 2.8 2.6 7.6 0 10.4" fill="none" stroke="#f3f3f3" stroke-width="0.8"/></svg>brinmoortech.com</li>
    </ul>
  </section>

  <section class="card card-back">
    <div class="wordmark">
      <span class="wordmark-name">BRINMOOR</span>
      <span class="wordmark-dot"></span>
    </div>
    <p class="tagline">A Cloud Consulting Company</p>
  </section>
</body>
</html>
```